Business card

We need a business card design for our company based in Auckland , New Zealand called 'Ridge + Studio Ltd'. We provide architectural services. We would like to see designs that use the max. three colours (such as white, black, grey) The final design should communicate financial safety and growth."
Also I will provide our company logo. I would like to the logo to be embeded onto our business card.

Target Market(s)

new residential house, alteration & addition & light commericila design & drafting service

Industry/Entity Type

Architecture

Contact Information for Business Card

Company name: ridge + studio Ltd.
Name: Mark Delford
Job title: architectural designer & Design LBP
email address: mark@rplusd.co.nz
mobile number: 02 5163 2290
web site: www.rplusd.co.nz

Requirements
Must have
• My project must have..
• - embeded logo (attached company logo)
• I don't have a bigger version for our company logo, but I have one old one, so you can remove the word from it)
• - insert the attached small BKTW logo & LBP logo
• - creative, simple and clear business card.
• - Max. three colours
Nice to have
• - Here are the samples I would like to share with you: http://www.plimvora.com/blog/minimalistic-business-card-designs/
• I would like to have my business card like one of the creation.
Should not have
• TBA

```html
<!DOCTYPE html>
<html lang="en">
<head>
<meta charset="utf-8">
<title>Ridge + Studio Ltd — Business Card</title>
<link rel="stylesheet" href="https://fonts.googleapis.com/css2?family=Questrial&family=Source+Sans+3:wght@400;600&display=swap">
<style>
  :root {
    --backdrop: #bdbdbd;
    --card-light: #ffffff;
    --card-dark: #000000;
    --ink: #111111;
    --ink-soft: #222222;
    --paper: #ffffff;
  }
  * { margin: 0; padding: 0; box-sizing: border-box; }
  html, body {
    width: 1200px;
    height: 900px;
    overflow: hidden;
    background: var(--backdrop);
  }
  .stage { position: relative; width: 1200px; height: 900px; }
  .card {
    position: absolute;
    top: 170px;
    width: 347px;
    height: 561px;
  }
  .card--front { left: 259px; background: var(--card-light); color: var(--ink); }
  .card--back { left: 631px; background: var(--card-dark); color: var(--paper); }

  .brand-mark { position: absolute; display: block; }
  .brand-name {
    position: absolute;
    left: 0; right: 0;
    font-family: "Questrial", sans-serif;
    white-space: nowrap;
    line-height: 1.2;
  }
  .card--front .brand-mark { left: 132px; top: 63px; }
  .card--front .brand-name { top: 183px; padding-left: 65px; font-size: 20px; }
  .card--back .brand-mark { left: 109px; top: 65px; }
  .card--back .brand-name { top: 203px; text-align: center; font-size: 22px; }

  .person { position: absolute; left: 39px; top: 358px; font-family: "Source Sans 3", sans-serif; }
  .person__name { font-size: 19px; font-weight: 600; line-height: 1.2; }
  .person__title { font-size: 15px; line-height: 1.35; color: var(--ink-soft); }

  .contacts {
    position: absolute; left: 39px; top: 441px;
    list-style: none;
    font-family: "Source Sans 3", sans-serif;
    font-size: 15px; color: var(--ink-soft);
  }
  .contacts li { display: flex; align-items: center; height: 20px; }
  .contacts svg { width: 11px; height: 11px; margin-right: 10px; fill: var(--ink); flex: none; }

  .badge { position: absolute; display: block; }
  .badge--certification { left: 122px; top: 283px; }
  .badge--membership { left: 116px; top: 414px; }
</style>
</head>
<body>
<main class="stage">
  <section class="card card--front" aria-label="Business card front">
    <svg class="brand-mark" width="116" height="116" viewBox="0 0 116 116" aria-hidden="true">
      <circle cx="58" cy="58" r="54" fill="none" stroke="var(--ink)" stroke-width="6"/>
    </svg>
    <p class="brand-name">ridge + studio Ltd.</p>

    <div class="person">
      <p class="person__name">Mark Delford</p>
      <p class="person__title">Architectural designer &amp; Design LBP</p>
    </div>

    <ul class="contacts">
      <li>
        <svg viewBox="0 0 24 24" aria-hidden="true"><path d="M6.6 10.8c1.4 2.8 3.8 5.1 6.6 6.6l2.2-2.2c.3-.3.7-.4 1-.2 1.1.4 2.3.6 3.6.6.6 0 1 .4 1 1V20c0 .6-.4 1-1 1C10.6 21 3 13.4 3 4c0-.6.4-1 1-1h3.5c.6 0 1 .4 1 1 0 1.3.2 2.5.6 3.6.1.3 0 .7-.2 1L6.6 10.8z"/></svg>
        02 5163 2290
      </li>
      <li>
        <svg viewBox="0 0 24 24" aria-hidden="true"><path d="M2 5h20v14H2z M2 5l10 7 10-7" stroke="var(--paper)" stroke-width="1.5"/></svg>
        mark@rplusd.co.nz
      </li>
      <li>
        <svg viewBox="0 0 24 24" aria-hidden="true"><circle cx="12" cy="12" r="10"/></svg>
        www.rplusd.co.nz
      </li>
    </ul>
  </section>

  <section class="card card--back" aria-label="Business card back">
    <svg class="brand-mark" width="130" height="130" viewBox="0 0 130 130" aria-hidden="true">
      <circle cx="65" cy="65" r="61" fill="none" stroke="var(--paper)" stroke-width="6"/>
    </svg>
    <p class="brand-name">ridge + studio Ltd.</p>

    <svg class="badge badge--certification" width="104" height="104" viewBox="0 0 104 104" role="img" aria-label="Practitioner certification badge">
      <circle cx="52" cy="52" r="51" fill="var(--paper)"/>
      <circle cx="52" cy="52" r="38" fill="var(--ink-soft)"/>
    </svg>

    <svg class="badge badge--membership" width="116" height="80" viewBox="0 0 116 80" role="img" aria-label="Professional membership badge">
      <rect x="0" y="0" width="116" height="80" fill="var(--paper)"/>
    </svg>
  </section>
</main>
</body>
</html>
```